We need a modern WIX website for Brightform Beam Services Australia (Laser/Industrial/Engineering)

We need a website for Wix (coded) for our laser restoration and industrial cleaning business.

It will need to be 4-6 pages.
Pages may include:
Home
About
Why Laser
Capabilities
There needs to be a contact / quote form

We do not want boring institutional design, so please do try to be a little creative (but not artsy, more engineering / laser etc). We hesitate with boxy wordpress looking templates, so please bring in strip backgrounds and sliders etc;

Our brand colours are blue and red, but a sharp modern site relative to the industry and work is important.

We envision the home page to take visitors on a informed journey of who, what, why, how, explaining the capability of laser science across contaminants, industries and surfaces.

We envision the home page to be strips:
- landing
- intro

-Why choose laser / What is laser cleaning
Minimum downtime, no surface damage, no environmental impact, no mess, no waste, complete restoration (we have an explainer video)

- Contaminants
Bacteria, Rust, Corrosion, Oxides, Grease, Oil, Paint, Stains, Mold, Soot / Carbon, Graffiti, Coatings, Dirt, Residue

- Surfaces
Metals, Engines/Parts/Components, Tools, Machinery, Bricks/Blockwork, Concrete, Paint, Stone, Wood, Aluminium

- Industries
Medical/Sterile, Hospitality, Bio Hazardous, Construction, Infrastructure, Property, Industrial, Engineer, Automotive, Marine, Heritage, Non Destructive Testing,

----
Here is some info on the company below:

"Background Information - Brightform Beam Services Australia (BBSA) is a leading provider of advanced laser restoration services for the residential, commercial, medical, hazardous and industrial sectors, offering waste free, chemical free and damage free complete restoration of metals, concrete, wood, stone and heritage, hygiene and hazard surfaces, with complete removal of coatings, bacteria, paint, rust, graffiti, mold and fire ash (soot), and preparation and treating for welding and bonding.
Servicing Melbourne and Victoria, with additional services available Australia wide, BBSA offers a 24/7 call-out service to your site.
With no downtime to your operations, we offer a timely resolution to your cleaning and maintenance needs."

We have attached some inspiration of websites we like the flow/feel of, but feel free to put your best designs forward.

You are welcome to use dummy headers and text at this stage, as design and feel is most important, and we can add text later.

```html
<!DOCTYPE html>
<html lang="en">
<head>
<meta charset="utf-8">
<title>Brightform Beam Services Australia – Home</title>
<link href="https://fonts.googleapis.com/css2?family=Michroma&family=Poppins:wght@400;500;600;700&family=Oswald:wght@600&display=swap" rel="stylesheet">
<style>
:root{
  --red:#e3151e;--red-dark:#b40f16;--blue:#1a63b8;--blue-dark:#0f4a8f;--navy:#0c1f3d;
  --black:#0a0a0c;--ink:#2a2a2a;--muted:#666;--canvas:#3b3b3d;--white:#fff;--line:#d8d8d8;
  --head:"Michroma",sans-serif;--body:"Poppins",sans-serif;--label:"Oswald",sans-serif;
}
*{box-sizing:border-box;margin:0;padding:0}
html,body{width:1200px;height:3003px;overflow:hidden;background:var(--canvas);font-family:var(--body);color:var(--ink)}
.page{position:absolute;width:534px;background:var(--white);overflow:hidden}
.page-a{left:47px;top:26px}
.page-b{left:619px;top:31px}
section,header,footer{position:relative;overflow:hidden}

.topbar{height:26px;background:var(--red);color:var(--white);display:flex;align-items:center;gap:22px;padding-left:48px;font:5.5px var(--head);letter-spacing:.3px}
.topbar span::before{content:"";display:inline-block;width:5px;height:5px;border:1px solid var(--white);border-radius:1px;margin-right:6px;vertical-align:-1px}
.nav{height:38px;display:flex;align-items:center;justify-content:space-between;padding:0 46px 0 48px;background:var(--white)}
.brand{display:flex;align-items:center;gap:4px;font:700 17px var(--body);color:var(--red);letter-spacing:.5px}
.brand i{width:9px;height:9px;border-radius:50%;background:var(--blue);display:block}
.menu{display:flex;align-items:center;gap:12px;font:600 5.6px var(--body);letter-spacing:.4px;text-transform:uppercase}
.menu .on{color:var(--red);border-bottom:1px solid var(--red)}
.menu .cta{background:var(--blue);color:var(--white);padding:6px 8px;font-weight:600}

.btn{display:inline-flex;align-items:center;gap:5px;background:var(--white);color:var(--black);font:6px var(--head);padding:4px 8px 4px 4px;border-radius:1px;white-space:nowrap}
.btn i{width:14px;height:14px;background:var(--blue);border-top:3px solid var(--red);display:block}
.btn.red{background:var(--red);color:var(--white)}
.btn.red i{background:var(--white);border-top-color:var(--blue)}

.hero{height:270px;background:var(--blue)}
.hero .photo{position:absolute;inset:0;background:radial-gradient(circle at 72% 55%,#ffb347 0,#c4551d 10%,#3c2418 26%,transparent 45%),linear-gradient(110deg,#0d1422 0%,#1b2a44 50%,#2b3a55 100%)}
.hero svg{position:absolute;inset:0}
.hero-copy{position:absolute;left:49px;top:46px;color:var(--white)}
.kicker{font:6px var(--label);letter-spacing:1px;text-transform:uppercase}
.hero h1{font:400 13.5px/23px var(--head);letter-spacing:.6px;margin:10px 0 10px;text-transform:uppercase}

.about{height:319px;background:var(--blue);color:var(--white)}
.about .vert{position:absolute;left:4px;top:268px;transform:rotate(-90deg);transform-origin:0 0;font:48px var(--head);color:transparent;-webkit-text-stroke:.7px rgba(255,255,255,.25);letter-spacing:8px}
.about .shot{position:absolute;left:80px;top:62px;width:166px;height:235px;border:3px solid var(--white);background:radial-gradient(circle at 50% 80%,#ffd27a 0,#d0692a 12%,transparent 30%),linear-gradient(180deg,#20252d,#5a6b7d 60%,#27313d)}
.about .txt{position:absolute;left:280px;top:70px;width:215px}
.eyebrow{font:6px var(--label);letter-spacing:1.2px;color:var(--red);text-transform:uppercase}
.about .eyebrow{color:var(--white)}
.title{font:400 10.5px/17px var(--head);letter-spacing:.5px;text-transform:uppercase;display:flex;align-items:flex-start;gap:4px}
.title b{width:8px;height:8px;background:var(--red);border-left:4px solid var(--blue);margin-top:4px;flex:none}
.about .title{margin:6px 0 9px}
.about p{font:5px/9.6px var(--body);margin-bottom:12px}

.ghost{position:absolute;left:0;right:0;text-align:center;font:44px var(--head);color:transparent;-webkit-text-stroke:.7px rgba(0,0,0,.13);letter-spacing:9px;white-space:nowrap}
.ghost.light{-webkit-text-stroke-color:rgba(255,255,255,.22)}
.heading{position:absolute;left:0;right:0;text-align:center}
.heading .title{justify-content:center;margin-top:3px}

.how{height:365px}
.how svg.paths{position:absolute;left:0;top:0}
.step{position:absolute;width:100px;margin-left:-50px;text-align:center;font:5.3px/10px var(--head);text-transform:uppercase}
.ring{width:72px;height:72px;margin:0 auto 6px;border-radius:50%;background:var(--white);border:6px solid var(--red);box-shadow:0 0 0 4px #f1c9cb;display:flex;align-items:center;justify-content:center}
.ring i{width:26px;height:26px;border:2px solid var(--red);border-radius:50%;display:block}
.how .copy{position:absolute;left:68px;right:68px;top:248px;text-align:center;font:5.2px/10px var(--body);color:#333}
.how .copy p{margin-bottom:10px}

.compare{height:260px;background:linear-gradient(135deg,var(--red) 0%,#cf1119 50%,var(--red) 100%);color:var(--white)}
.table{position:absolute;left:49px;top:73px;width:436px;height:154px;background:var(--white);display:grid;grid-template-columns:1fr 1fr;grid-template-rows:24px 1fr}
.table .th{font:5.3px/8px var(--head);text-align:center;color:var(--white);display:flex;align-items:center;justify-content:center;text-transform:uppercase}
.table .th.a{background:var(--blue)}.table .th.b{background:#3d3d3f}
.table ul{list-style:none;padding:8px 10px;font:5px/8.2px var(--body);color:#333}
.table ul+ul{border-left:1px solid var(--line)}
.table li{margin-bottom:5px;padding-left:7px;text-indent:-7px}
.table li::before{content:"→ ";color:var(--blue)}

.why{height:224px}
.row{position:absolute;left:49px;right:49px;display:flex;justify-content:space-between}
.tri{width:80px;text-align:center;font:5.4px/10px var(--head);text-transform:uppercase}
.tri svg{display:block;margin:0 auto 4px}
.arrow{position:absolute;width:11px;height:11px;border-radius:50%;background:var(--black)}
.arrow.w{background:var(--white)}

.contam{height:239px;background:linear-gradient(120deg,var(--blue) 0%,var(--blue-dark) 100%);color:var(--white)}
.tiles{position:absolute;left:49px;top:72px;width:436px;display:flex;justify-content:space-between}
.tile{width:101px;height:140px;display:flex;align-items:center;justify-content:center;font:600 7px var(--body);color:var(--white);text-transform:uppercase;text-shadow:0 0 3px #000}
.t-bac{background:radial-gradient(circle at 40% 50%,#7a9b3a,#2e4d2a 45%,#1b2a1d)}
.t-rust{background:linear-gradient(135deg,#a25a22,#7a3c14 50%,#9c5524)}
.t-cor{background:linear-gradient(160deg,#c9a35a,#6a5a44 50%,#3d3a3a)}
.t-oxi{background:linear-gradient(135deg,#2a2a2a,#9a9a9a 40%,#3a3a3a 70%,#cfcfcf)}

.video{height:239px;background:linear-gradient(180deg,var(--blue-dark) 0 46%,var(--white) 46% 100%)}
.player{position:absolute;left:49px;top:8px;width:436px;height:219px;border:2px solid var(--red);border-radius:6px;background:radial-gradient(circle at 55% 50%,#ffcf7a 0,#c06520 14%,#3b2a22 38%,#141820 70%);overflow:hidden}
.player .play{position:absolute;left:50%;top:50%;width:20px;height:20px;margin:-10px;border-radius:50%;background:var(--red)}
.player .play::after{content:"";position:absolute;left:8px;top:6px;border-left:6px solid var(--white);border-top:4px solid transparent;border-bottom:4px solid transparent}
.player .tag{position:absolute;right:16px;top:14px;font:700 11px var(--body);color:var(--white);letter-spacing:1px}

.surfaces{height:198px}
.industries{height:274px}
.cards{position:absolute;left:49px;top:70px;width:436px;display:flex;justify-content:space-between}
.card{width:139px;height:160px;display:flex;align-items:flex-end;justify-content:center;padding-bottom:10px;font:600 6.5px var(--body);color:var(--white);text-transform:uppercase}
.c-con{background:linear-gradient(180deg,#b7c3cf,#5c6470 55%,#22272e)}
.c-ind{background:radial-gradient(circle at 50% 45%,#f0b060 0,#5b4a6a 25%,#1b2540 65%)}
.c-auto{background:linear-gradient(135deg,#0f3c78,#3a8ad1 50%,#0f2c55)}

.contact{height:297px;background:linear-gradient(135deg,var(--red),#c40f18 60%,var(--red));color:var(--white)}
.form{position:absolute;left:78px;top:88px;width:378px}
.fields{display:flex;gap:5px;margin-bottom:6px}
.field{flex:1;height:20px;background:var(--white);font:5px var(--body);color:#777;padding:6px 7px}
.field.msg{height:40px;flex:none}
.form .btn{position:absolute;left:136px;top:82px}
.contact svg{position:absolute;left:0;bottom:0}

.footer{position:relative;height:183px;background:var(--black);color:var(--white)}
.footer .brand{position:absolute;left:49px;top:24px;color:var(--white);font-size:16px}
.footer .social{position:absolute;left:49px;top:54px;display:flex;gap:4px}
.footer .social i{width:9px;height:9px;background:var(--red);display:block}
.col{position:absolute;top:18px;font:5px/8px var(--body);color:var(--white)}
.col h4{font:6px var(--head);margin-bottom:8px;font-weight:400}
.col .email{width:104px;height:20px;background:var(--blue);padding:6px 8px;margin:7px 0 6px}
.col ul{list-style:none}
.col li{margin-bottom:7px}
.col li::before{content:"→ "}
.col .ci{display:flex;gap:6px;margin-bottom:10px}
.col .ci i{width:10px;height:10px;border:1px solid var(--white);display:block;flex:none}
.footer .legal{position:absolute;left:49px;right:49px;bottom:12px;border-top:1px solid #333;padding-top:9px;text-align:center;font:4.6px var(--body);color:#ccc}
</style>
</head>
<body>

<!-- ================= VERSION A ================= -->
<div class="page page-a">
  <div class="topbar"><span>CALL:+1 555 010 0199</span><span>MAIL:INFO@BBSA-DEMO.COM</span></div>
  <header class="nav">
    <div class="brand"><i></i>BBSA</div>
    <nav class="menu"><span class="on">Home</span><span>About</span><span>Why Laser</span><span>Capabilities</span><span class="cta">Contact Us</span></nav>
  </header>

  <section class="hero">
    <div class="photo" role="img" aria-label="Laser cutting head throwing sparks over a metal sheet"></div>
    <svg width="534" height="270" viewBox="0 0 534 270"><polygon points="0,190 267,262 534,190 534,270 0,270" fill="#1a63b8"/><polyline points="0,186 267,258 534,186" fill="none" stroke="#e3151e" stroke-width="5"/><circle cx="267" cy="252" r="10" fill="#fff"/></svg>
    <div class="hero-copy">
      <div class="kicker">Brightform Beam Services Australia</div>
      <h1>We are a laser restoration<br>and industrial cleaning<br>business</h1>
      <span class="btn"><i></i>GET STARTED</span>
    </div>
  </section>

  <section class="about">
    <div class="vert">ABOUT</div>
    <div class="shot" role="img" aria-label="Close-up of a laser head working on metal"></div>
    <div class="txt">
      <div class="eyebrow">About Us</div>
      <div class="title"><b></b>Welcome to Brightform Beam Services Australia</div>
      <p>Brightform Beam Services Australia (BBSA) is a leading provider of advanced laser restoration services for the residential, commercial, medical, hazardous and industrial sectors, offering waste free, chemical free and damage free complete restoration of metals, concrete, wood, stone and heritage, hygiene and hazard surfaces, with complete removal of coatings, bacteria, paint, rust, graffiti, mold and fire ash (soot), and preparation and treating for welding and bonding.</p>
      <p>Servicing Melbourne and Victoria, with additional services available Australia wide, BBSA offers a 24/7 call-out service to your site.</p>
      <span class="btn"><i></i>READ MORE</span>
    </div>
  </section>

  <section class="how">
    <div class="ghost" style="top:14px">CLEANING</div>
    <div class="heading" style="top:28px"><div class="eyebrow">How Its Work</div><div class="title"><b></b>What is laser cleaning ?</div></div>
    <svg class="paths" width="534" height="240"><path d="M97 118 C110 70 170 70 212 76 M212 76 C250 80 290 100 330 118 M330 118 C350 70 390 60 445 76" fill="none" stroke="#999" stroke-width=".8" stroke-dasharray="3 3"/></svg>
    <div class="step" style="left:97px;top:116px"><div class="ring"><i></i></div>Nanosecond-length<br>pulses of laser<br>light</div>
    <div class="step" style="left:212px;top:72px"><div class="ring"><i></i></div>Contaminated<br>surface</div>
    <div class="step" style="left:330px;top:116px"><div class="ring"><i></i></div>Contaminants<br>absorb laser<br>light</div>
    <div class="step" style="left:445px;top:72px"><div class="ring"><i></i></div>The<br>contaminants<br>will turn into<br>a gas</div>
    <div class="copy">
      <p>Laser cleaning technology works by sending nanosecond-length pulses of laser light towards a surface. When it interacts with contaminants that absorb laser light, the contaminants or coating particles will either turn into a gas or the pressure of the interaction will cause particles to free from the surface.</p>
      <p>With the right laser settings and equipment, laser cleaning is unmatched in its ability to clean all the way to the bare metal of your product. Our team specializes in the know-how and application of laser cleaning solutions to put together the formula for your specific situation. Once we identify the combination of settings and equipment, the process can be matched across other setups – working very efficiently without affecting the integrity of the surface you are cleaning.</p>
    </div>
  </section>

  <section class="compare">
    <div class="ghost light" style="top:10px">COMPARISON</div>
    <div class="heading" style="top:30px"><div class="eyebrow" style="color:#fff">BBSA</div><div class="title"><b style="background:#fff"></b>Table comparison</div></div>
    <div class="table">
      <div class="th a">Laser</div><div class="th b">Others<br>(chemical / sandblasting / dry ice)</div>
      <ul><li>Fast contact free removal with no abrasive media and no surface wear left behind</li><li>Precise beam control keeps the base material fully intact after each pass</li><li>Zero chemicals and no secondary waste stream to collect or dispose</li><li>Minimal setup on site so operations continue with very little downtime</li></ul>
      <ul><li>Abrasive media wears the surface and leaves grit that must be cleaned up</li><li>Chemical agents need handling, storage and careful disposal on site</li><li>Large containment is needed, slowing work and raising labour costs</li><li>Results vary between operators and surfaces often need refinishing</li></ul>
    </div>
  </section>

  <section class="why">
    <div class="ghost" style="top:12px">LASER</div>
    <div class="heading" style="top:30px"><div class="eyebrow">Laser</div><div class="title"><b></b>Why choose laser</div></div>
    <span class="arrow" style="left:17px;top:122px"></span><span class="arrow" style="right:17px;top:122px"></span>
    <div class="row" style="top:86px">
      <div class="tri"><svg width="80" height="76"><path d="M40 8 L74 68 L6 68 Z" fill="#e3151e" stroke="#e3151e" stroke-width="9" stroke-linejoin="round"/><circle cx="40" cy="48" r="11" fill="none" stroke="#fff" stroke-width="2"/></svg>Minimum<br>downtime</div>
      <div class="tri"><svg width="80" height="76"><path d="M6 8 L74 8 L40 68 Z" fill="#1a63b8" stroke="#1a63b8" stroke-width="9" stroke-linejoin="round"/><rect x="31" y="19" width="18" height="18" fill="none" stroke="#fff" stroke-width="2"/></svg>No surface<br>damage</div>
      <div class="tri"><svg width="80" height="76"><path d="M40 8 L74 68 L6 68 Z" fill="#e3151e" stroke="#e3151e" stroke-width="9" stroke-linejoin="round"/><path d="M31 40 L49 56 M49 40 L31 56" stroke="#fff" stroke-width="2.5"/></svg>No<br>mess</div>
      <div class="tri"><svg width="80" height="76"><path d="M6 8 L74 8 L40 68 Z" fill="#1a63b8" stroke="#1a63b8" stroke-width="9" stroke-linejoin="round"/><circle cx="40" cy="28" r="10" fill="none" stroke="#fff" stroke-width="2" stroke-dasharray="12 4"/></svg>Complete<br>restoration</div>
      <div class="tri"><svg width="80" height="76"><path d="M40 8 L74 68 L6 68 Z" fill="#e3151e" stroke="#e3151e" stroke-width="9" stroke-linejoin="round"/><circle cx="40" cy="48" r="10" fill="none" stroke="#fff" stroke-width="2"/><path d="M33 41 L47 55" stroke="#fff" stroke-width="2"/></svg>No<br>waste</div>
    </div>
  </section>

  <section class="contam">
    <div class="ghost light" style="top:12px">TREAT</div>
    <div class="heading" style="top:30px"><div class="eyebrow" style="color:#fff">Containments</div><div class="title"><b style="background:#fff"></b>Contaminants we treat</div></div>
    <span class="arrow w" style="left:17px;top:137px"></span><span class="arrow w" style="right:17px;top:137px"></span>
    <div class="tiles">
      <div class="tile t-bac" role="img" aria-label="Magnified bacteria">Bacteria</div>
      <div class="tile t-rust" role="img" aria-label="Rusted steel plate">Rust</div>
      <div class="tile t-cor" role="img" aria-label="Worker inspecting corroded machinery">Corrosion</div>
      <div class="tile t-oxi" role="img" aria-label="Oxidised crinkled metal foil">Oxides</div>
    </div>
  </section>

  <section class="video">
    <div class="player" role="img" aria-label="Explainer video still of a laser cutting metal with sparks"><span class="tag">BBSA</span><span class="play"></span></div>
  </section>

  <section class="surfaces">
    <div class="ghost" style="top:12px">SURFACES</div>
    <div class="heading" style="top:30px"><div class="eyebrow">BBSA</div><div class="title"><b></b>Our surfaces</div></div>
    <span class="arrow" style="left:17px;top:110px"></span><span class="arrow" style="right:17px;top:110px"></span>
    <div class="row" style="top:68px;align-items:flex-end">
      <div class="tri"><svg width="80" height="76"><path d="M40 8 L74 68 L6 68 Z" fill="#e3151e" stroke="#e3151e" stroke-width="9" stroke-linejoin="round"/><path d="M30 56 L48 38 M34 60 L52 42" stroke="#fff" stroke-width="2"/></svg>Metals</div>
      <div class="tri"><svg width="80" height="76"><path d="M6 8 L74 8 L40 68 Z" fill="#1a63b8" stroke="#1a63b8" stroke-width="9" stroke-linejoin="round"/><path d="M30 18 L50 38 M50 18 L30 38" stroke="#fff" stroke-width="2.5"/></svg>Tools</div>
      <div class="tri" style="color:#e3151e"><svg width="96" height="90"><path d="M48 8 L89 82 L7 82 Z" fill="#5a2b22" stroke="#e3151e" stroke-width="6" stroke-linejoin="round" role="img" aria-label="Machinery photo in triangle frame"/><rect x="38" y="48" width="20" height="16" fill="none" stroke="#fff" stroke-width="2"/></svg>Machinery</div>
      <div class="tri"><svg width="80" height="76"><path d="M6 8 L74 8 L40 68 Z" fill="#1a63b8" stroke="#1a63b8" stroke-width="9" stroke-linejoin="round"/><rect x="32" y="16" width="16" height="8" fill="none" stroke="#fff" stroke-width="2"/><path d="M40 24 L40 40" stroke="#fff" stroke-width="2.5"/></svg>Paint</div>
      <div class="tri"><svg width="80" height="76"><path d="M40 8 L74 68 L6 68 Z" fill="#e3151e" stroke="#e3151e" stroke-width="9" stroke-linejoin="round"/><path d="M28 42 L52 38 M28 48 L52 44 M28 54 L52 50 M28 60 L52 56" stroke="#fff" stroke-width="2"/></svg>Aluminium</div>
    </div>
  </section>

  <section class="industries">
    <div class="ghost" style="top:12px">INDUSTRIES</div>
    <div class="heading" style="top:30px"><div class="eyebrow">BBSA</div><div class="title"><b></b>Industries we serve</div></div>
    <div class="cards">
      <div class="card c-con" role="img" aria-label="Construction site at dusk">Construction</div>
      <div class="card c-ind" role="img" aria-label="Industrial welding sparks">Industrial</div>
      <div class="card c-auto" role="img" aria-label="Car on a digital inspection display">Automotive</div>
    </div>
  </section>

  <section class="contact">
    <div class="ghost light" style="top:16px">CONTACT US</div>
    <div class="heading" style="top:34px"><div class="eyebrow" style="color:#fff">BBSA</div><div class="title"><b style="background:#fff"></b>Get in touch with us</div></div>
    <div class="form">
      <div class="fields"><div class="field">Full Name</div><div class="field">Phone Number</div><div class="field">Email Address</div></div>
      <div class="field msg">Message</div>
      <span class="btn"><i></i>SEND MESSAGE</span>
    </div>
    <svg width="534" height="80"><polygon points="0,80 0,66 267,18 534,66 534,80" fill="#0a0a0c"/><polyline points="0,62 267,14 534,62" fill="none" stroke="#1a63b8" stroke-width="4"/><circle cx="267" cy="22" r="10" fill="#fff"/></svg>
  </section>

  <footer class="footer">
    <div class="brand"><i></i>BBSA</div>
    <div class="social"><i></i><i></i><i></i><i></i></div>
    <div class="col" style="left:170px"><h4>SUBSCRIBE US</h4>BBSA offers a 24/7 call-out service to<br>your site<div class="email">Enter The Email</div><span class="btn red"><i></i>Subscribe</span></div>
    <div class="col" style="left:308px"><h4>CONTACT US</h4><div class="ci"><i></i><span>BBSA<br>Sample District</span></div><div class="ci"><i></i><span>+1 555 010 0199</span></div><div class="ci"><i></i><span>info@bbsa-demo.com</span></div></div>
    <div class="col" style="left:413px"><h4>QUICK LINKS</h4><ul><li>Home</li><li>About</li><li>Why Laser</li><li>Capabilities</li><li>Contact Us</li></ul></div>
    <div class="legal">Copyrights@2023 Brightform Beam Services Australia.All Rights Reserved</div>
  </footer>
</div>

<!-- ================= VERSION B ================= -->
<div class="page page-b">
  <div class="topbar"><span>CALL:+1 555 010 0199</span><span>MAIL:INFO@BBSA-DEMO.COM</span></div>
  <header class="nav">
    <div class="brand"><i></i>BBSA</div>
    <nav class="menu"><span class="on">Home</span><span>About</span><span>Why Laser</span><span>Capabilities</span><span class="cta">Contact Us</span></nav>
  </header>

  <section class="hero">
    <div class="photo" role="img" aria-label="Laser cutting head throwing sparks over a metal sheet"></div>
    <svg width="534" height="270" viewBox="0 0 534 270"><polygon points="0,190 267,262 534,190 534,270 0,270" fill="#1a63b8"/><polyline points="0,186 267,258 534,186" fill="none" stroke="#e3151e" stroke-width="5"/><circle cx="267" cy="252" r="10" fill="#fff"/></svg>
    <div class="hero-copy">
      <div class="kicker">Brightform Beam Services Australia</div>
      <h1>We are a laser restoration<br>and industrial cleaning<br>business</h1>
      <span class="btn"><i></i>GET STARTED</span>
    </div>
  </section>

  <section class="about">
    <div class="vert">ABOUT</div>
    <div class="shot" role="img" aria-label="Close-up of a laser head working on metal"></div>
    <div class="txt">
      <div class="eyebrow">About Us</div>
      <div class="title"><b></b>Welcome to Brightform Beam Services Australia</div>
      <p>Brightform Beam Services Australia (BBSA) is a leading provider of advanced laser restoration services for the residential, commercial, medical, hazardous and industrial sectors, offering waste free, chemical free and damage free complete restoration of metals, concrete, wood, stone and heritage, hygiene and hazard surfaces, with complete removal of coatings, bacteria, paint, rust, graffiti, mold and fire ash (soot), and preparation and treating for welding and bonding.</p>
      <p>Servicing Melbourne and Victoria, with additional services available Australia wide, BBSA offers a 24/7 call-out service to your site.</p>
      <span class="btn"><i></i>READ MORE</span>
    </div>
  </section>

  <section class="video" style="height:230px;background:linear-gradient(180deg,var(--blue) 0 55%,var(--white) 55% 100%)">
    <div class="player" role="img" aria-label="Explainer video still of a laser cutting metal with sparks"><span class="tag">BBSA</span><span class="play"></span></div>
  </section>

  <section class="how" style="height:367px">
    <div class="ghost" style="top:14px">CLEANING</div>
    <div class="heading" style="top:28px"><div class="eyebrow">How Its Work</div><div class="title"><b></b>What is laser cleaning ?</div></div>
    <svg class="paths" width="534" height="240"><path d="M97 118 C110 70 170 70 212 76 M212 76 C250 80 290 100 330 118 M330 118 C350 70 390 60 445 76" fill="none" stroke="#999" stroke-width=".8" stroke-dasharray="3 3"/></svg>
    <div class="step" style="left:97px;top:116px"><div class="ring"><i></i></div>Nanosecond-length<br>pulses of laser<br>light</div>
    <div class="step" style="left:212px;top:72px"><div class="ring"><i></i></div>Contaminated<br>surface</div>
    <div class="step" style="left:330px;top:116px"><div class="ring"><i></i></div>Contaminants<br>absorb laser<br>light</div>
    <div class="step" style="left:445px;top:72px"><div class="ring"><i></i></div>The<br>contaminants<br>will turn into<br>a gas</div>
    <div class="copy">
      <p>Laser cleaning technology works by sending nanosecond-length pulses of laser light towards a surface. When it interacts with contaminants that absorb laser light, the contaminants or coating particles will either turn into a gas or the pressure of the interaction will cause particles to free from the surface.</p>
      <p>With the right laser settings and equipment, laser cleaning is unmatched in its ability to clean all the way to the bare metal of your product. Our team specializes in the know-how and application of laser cleaning solutions to put together the formula for your specific situation. Once we identify the combination of settings and equipment, the process can be matched across other setups – working very efficiently without affecting the integrity of the surface you are cleaning.</p>
    </div>
  </section>

  <section class="compare" style="height:259px">
    <div class="ghost light" style="top:10px">COMPARISON</div>
    <div class="heading" style="top:30px"><div class="eyebrow" style="color:#fff">BBSA</div><div class="title"><b style="background:#fff"></b>Table comparison</div></div>
    <div class="table">
      <div class="th a">Laser</div><div class="th b">Others<br>(chemical / sandblasting / dry ice)</div>
      <ul><li>Fast contact free removal with no abrasive media and no surface wear left behind</li><li>Precise beam control keeps the base material fully intact after each pass</li><li>Zero chemicals and no secondary waste stream to collect or dispose</li><li>Minimal setup on site so operations continue with very little downtime</li></ul>
      <ul><li>Abrasive media wears the surface and leaves grit that must be cleaned up</li><li>Chemical agents need handling, storage and careful disposal on site</li><li>Large containment is needed, slowing work and raising labour costs</li><li>Results vary between operators and surfaces often need refinishing</li></ul>
    </div>
  </section>

  <section class="why" style="height:225px">
    <div class="ghost" style="top:12px">LASER</div>
    <div class="heading" style="top:30px"><div class="eyebrow">Laser</div><div class="title"><b></b>Why choose laser</div></div>
    <span class="arrow" style="left:17px;top:122px"></span><span class="arrow" style="right:17px;top:122px"></span>
    <div class="row" style="top:86px">
      <div class="tri"><svg width="80" height="76"><path d="M40 8 L74 68 L6 68 Z" fill="#e3151e" stroke="#e3151e" stroke-width="9" stroke-linejoin="round"/><circle cx="40" cy="48" r="11" fill="none" stroke="#fff" stroke-width="2"/></svg>Minimum<br>downtime</div>
      <div class="tri"><svg width="80" height="76"><path d="M6 8 L74 8 L40 68 Z" fill="#1a63b8" stroke="#1a63b8" stroke-width="9" stroke-linejoin="round"/><rect x="31" y="19" width="18" height="18" fill="none" stroke="#fff" stroke-width="2"/></svg>No surface<br>damage</div>
      <div class="tri"><svg width="80" height="76"><path d="M40 8 L74 68 L6 68 Z" fill="#e3151e" stroke="#e3151e" stroke-width="9" stroke-linejoin="round"/><path d="M31 40 L49 56 M49 40 L31 56" stroke="#fff" stroke-width="2.5"/></svg>No<br>mess</div>
      <div class="tri"><svg width="80" height="76"><path d="M6 8 L74 8 L40 68 Z" fill="#1a63b8" stroke="#1a63b8" stroke-width="9" stroke-linejoin="round"/><circle cx="40" cy="28" r="10" fill="none" stroke="#fff" stroke-width="2" stroke-dasharray="12 4"/></svg>Complete<br>restoration</div>
      <div class="tri"><svg width="80" height="76"><path d="M40 8 L74 68 L6 68 Z" fill="#e3151e" stroke="#e3151e" stroke-width="9" stroke-linejoin="round"/><circle cx="40" cy="48" r="10" fill="none" stroke="#fff" stroke-width="2"/><path d="M33 41 L47 55" stroke="#fff" stroke-width="2"/></svg>No<br>waste</div>
    </div>
  </section>

  <section class="contam" style="height:251px">
    <div class="ghost light" style="top:12px">TREAT</div>
    <div class="heading" style="top:30px"><div class="eyebrow" style="color:#fff">Containments</div><div class="title"><b style="background:#fff"></b>Contaminants we treat</div></div>
    <span class="arrow w" style="left:17px;top:137px"></span><span class="arrow w" style="right:17px;top:137px"></span>
    <div class="tiles">
      <div class="tile t-bac" role="img" aria-label="Magnified bacteria">Bacteria</div>
      <div class="tile t-rust" role="img" aria-label="Rusted steel plate">Rust</div>
      <div class="tile t-cor" role="img" aria-label="Worker inspecting corroded machinery">Corrosion</div>
      <div class="tile t-oxi" role="img" aria-label="Oxidised crinkled metal foil">Oxides</div>
    </div>
  </section>

  <section class="surfaces" style="height:222px">
    <div class="ghost" style="top:24px">SURFACES</div>
    <div class="heading" style="top:42px"><div class="eyebrow">BBSA</div><div class="title"><b></b>Our surfaces</div></div>
    <span class="arrow" style="left:17px;top:122px"></span><span class="arrow" style="right:17px;top:122px"></span>
    <div class="row" style="top:80px;align-items:flex-end">
      <div class="tri"><svg width="80" height="76"><path d="M40 8 L74 68 L6 68 Z" fill="#e3151e" stroke="#e3151e" stroke-width="9" stroke-linejoin="round"/><path d="M30 56 L48 38 M34 60 L52 42" stroke="#fff" stroke-width="2"/></svg>Metals</div>
      <div class="tri"><svg width="80" height="76"><path d="M6 8 L74 8 L40 68 Z" fill="#1a63b8" stroke="#1a63b8" stroke-width="9" stroke-linejoin="round"/><path d="M30 18 L50 38 M50 18 L30 38" stroke="#fff" stroke-width="2.5"/></svg>Tools</div>
      <div class="tri" style="color:#e3151e"><svg width="96" height="90"><path d="M48 8 L89 82 L7 82 Z" fill="#5a2b22" stroke="#e3151e" stroke-width="6" stroke-linejoin="round" role="img" aria-label="Machinery photo in triangle frame"/><rect x="38" y="48" width="20" height="16" fill="none" stroke="#fff" stroke-width="2"/></svg>Machinery</div>
      <div class="tri"><svg width="80" height="76"><path d="M6 8 L74 8 L40 68 Z" fill="#1a63b8" stroke="#1a63b8" stroke-width="9" stroke-linejoin="round"/><rect x="32" y="16" width="16" height="8" fill="none" stroke="#fff" stroke-width="2"/><path d="M40 24 L40 40" stroke="#fff" stroke-width="2.5"/></svg>Paint</div>
      <div class="tri"><svg width="80" height="76"><path d="M40 8 L74 68 L6 68 Z" fill="#e3151e" stroke="#e3151e" stroke-width="9" stroke-linejoin="round"/><path d="M28 42 L52 38 M28 48 L52 44 M28 54 L52 50 M28 60 L52 56" stroke="#fff" stroke-width="2"/></svg>Aluminium</div>
    </div>
  </section>

  <section class="industries" style="height:262px">
    <div class="ghost" style="top:6px">INDUSTRIES</div>
    <div class="heading" style="top:24px"><div class="eyebrow">BBSA</div><div class="title"><b></b>Industries we serve</div></div>
    <div class="cards" style="top:62px">
      <div class="card c-con" role="img" aria-label="Construction site at dusk">Construction</div>
      <div class="card c-ind" role="img" aria-label="Industrial welding sparks">Industrial</div>
      <div class="card c-auto" role="img" aria-label="Car on a digital inspection display">Automotive</div>
    </div>
  </section>

  <section class="contact" style="height:292px">
    <div class="ghost light" style="top:16px">CONTACT US</div>
    <div class="heading" style="top:34px"><div class="eyebrow" style="color:#fff">BBSA</div><div class="title"><b style="background:#fff"></b>Get in touch with us</div></div>
    <div class="form">
      <div class="fields"><div class="field">Full Name</div><div class="field">Phone Number</div><div class="field">Email Address</div></div>
      <div class="field msg">Message</div>
      <span class="btn"><i></i>SEND MESSAGE</span>
    </div>
    <svg width="534" height="80"><polygon points="0,80 0,66 267,18 534,66 534,80" fill="#0a0a0c"/><polyline points="0,62 267,14 534,62" fill="none" stroke="#1a63b8" stroke-width="4"/><circle cx="267" cy="22" r="10" fill="#fff"/></svg>
  </section>

  <footer class="footer">
    <div class="brand"><i></i>BBSA</div>
    <div class="social"><i></i><i></i><i></i><i></i></div>
    <div class="col" style="left:170px"><h4>SUBSCRIBE US</h4>BBSA offers a 24/7 call-out service to<br>your site<div class="email">Enter The Email</div><span class="btn red"><i></i>Subscribe</span></div>
    <div class="col" style="left:308px"><h4>CONTACT US</h4><div class="ci"><i></i><span>BBSA<br>Sample District</span></div><div class="ci"><i></i><span>+1 555 010 0199</span></div><div class="ci"><i></i><span>info@bbsa-demo.com</span></div></div>
    <div class="col" style="left:413px"><h4>QUICK LINKS</h4><ul><li>Home</li><li>About</li><li>Why Laser</li><li>Capabilities</li><li>Contact Us</li></ul></div>
    <div class="legal">Copyrights@2023 Brightform Beam Services Australia.All Rights Reserved</div>
  </footer>
</div>

</body>
</html>
```